Lurvik.no is a new website about pedagogical entrepreneurship. It's main target group is teachers. The Nordic Bureau for Digital Schooling and the National Office for Learning and Classrooms are leading the project.

The web page is meant to show examples of how different methods of entrepreneurship can be used pedagogical in a learning environment. The page will also support the user with examples of different teaching programs and other examples of best practice.

Pedagogical entrepreneurship is not about business and men in suits. It's a method for learning. The focus in the design should be on school, education and new ways of learning.

The final product should be motivating and engaging, but at the same time governmental and serious. We are not looking for something "flashy" and corporate-looking, but a moderate, task-focused and clean design that state quality.

We need designs for three pages:
1 - frontpage
2 - subpage ("Metoder og undervisningsopplegg")
3 - subpage ("Små-TOPP i Vassbygd")

The interaction design for these three pages will be uploaded as an attachment.

We would like you to find inspiration in the following websites:
- www.skapekraft.no
- www.giellu.no
- www.brightfernlab.com
- www.zyx.no
(more will be added)

Please use the attached logo, and feel free to use this as an inspiration for the rest of the design.

Target Market(s)

Teachers

Industry/Entity Type

Education

Requirements
Must have
• * Header with: Logo. Main navigation. Utility navigation. Search box.
* Footer
Should not have
• Images of men in suits.
Very strong graphical elements that stands out too much (we want it clean).

```html
<!DOCTYPE html>
<html lang="en">
<head>
<meta charset="utf-8">
<title>Små-TOPP i Vassbygd – Lurvik.no</title>
<link href="https://fonts.googleapis.com/css2?family=Arimo:wght@400;700&family=Bree+Serif&display=swap" rel="stylesheet">
<style>
:root{
  --navy:#1d3a66;
  --navy-dark:#142b4f;
  --blue:#2a88c8;
  --blue-deep:#0f3f6e;
  --link:#1f5a96;
  --green:#8ab51e;
  --text:#3a3a3a;
  --muted:#555;
  --pale:#e6eff8;
}
*{box-sizing:border-box;margin:0;padding:0}
html,body{width:960px;height:1200px;overflow:hidden;background:#fff}
body{position:relative;font-family:Arimo,Arial,sans-serif;color:var(--text)}
.abs{position:absolute}
.serif{font-family:"Bree Serif",Georgia,serif}

/* utility bar */
.utility-bar{left:0;top:0;width:960px;height:30px;background:var(--navy)}
.utility-nav{left:324px;top:9px;display:flex;gap:24px;font-size:10px;color:#fff}
.search{left:686px;top:6px;width:178px;height:17px;background:#fff;border-radius:9px;font-size:9px;color:#888;padding:3px 8px}
.search svg{position:absolute;right:6px;top:3px}

/* header */
.logo{left:96px;top:46px;display:flex;align-items:center;gap:10px}
.logo-mark{width:42px;height:42px;border-radius:50%;background:var(--blue)}
.logo-name{font-size:36px;font-weight:700;color:var(--blue);line-height:1}
.logo-tag{font-size:7px;color:var(--blue);margin-top:2px}
.feature{display:flex;gap:8px;top:51px}
.icon-circle{width:42px;height:42px;border-radius:50%;background:radial-gradient(circle at 50% 35%,#2d6fb0,var(--navy-dark));box-shadow:0 0 0 3px #fff,0 0 0 4px #cfd8e2;display:flex;align-items:center;justify-content:center;flex:none}
.feature h3{font-family:"Bree Serif",Georgia,serif;font-weight:400;font-size:11px;line-height:14px;color:#1b1b1b}
.feature em{font-family:"Bree Serif",Georgia,serif;font-size:10px;color:var(--green);display:block;margin-top:2px}
.band{left:0;top:114px;width:960px;height:25px;background:linear-gradient(#3a9ad6,#2379b9);border-top:1px solid #1f6ea8}

/* breadcrumb */
.crumbs{left:95px;top:159px;font-size:8.5px;display:flex;gap:12px}
.crumbs a{color:var(--link);text-decoration:none}
.social{top:157px;display:flex;gap:3px;font-size:8.5px;align-items:center}
.social .btn{border:1px solid #c8d0da;border-radius:2px;padding:2px 4px;background:#eef2f7;color:var(--link);display:flex;gap:3px;align-items:center}
.social .sq{width:8px;height:8px;background:var(--link)}
.social .count{border:1px solid #c8d0da;padding:2px 3px;background:#fff;color:#333}
.dash{height:0;border-top:1px dashed #999}
.dash.green{border-top-color:var(--green)}

/* intro */
.title{left:94px;top:204px;font-size:21px;color:var(--green)}
.lead{left:95px;top:244px;width:460px;font-size:12.5px;font-weight:700;line-height:16px;color:#2a2a2a}
.body{width:460px;font-size:10px;line-height:16px;color:var(--text)}
.fact{display:flex;gap:10px;align-items:center}
.fact b{display:block;font-size:12.5px;font-weight:400;color:#333}
.fact span{font-size:9.5px;font-weight:700;color:var(--green)}

/* school card */
.card-frame{border:1px solid #dde3ea;border-radius:5px;background:#fff;box-shadow:0 1px 3px rgba(0,0,0,.15)}
.school{left:654px;top:243px;width:208px;height:229px}
.school-inner{left:4px;top:4px;width:200px;height:221px;background:linear-gradient(#2d85c2,#12406f 60%,#0d2d52);border-radius:3px}
.school h4{font-size:12px;font-weight:700;color:#fff}
.school small{font-size:8px;color:#fff;font-weight:700}
.photo-school{left:16px;top:42px;width:168px;height:95px;border:1px solid #fff;background:linear-gradient(#c9d6df,#8d8f88 55%,#e6e9ea)}
.contact{left:16px;top:146px;width:168px;height:58px;background:#fff;border-radius:2px}
.contact small{font-size:8.5px;font-weight:700;color:#555}
.contact a{font-size:11px;color:var(--green);text-decoration:none}

/* content */
.h-sub{font-size:12px;font-weight:700;color:#2a2a2a}

/* multimedia */
.media{left:566px;top:527px;width:294px;height:308px}
.media-inner{left:4px;top:4px;width:286px;height:300px;background:linear-gradient(#2a86c4,#103e6c 55%,#0a2446);border-radius:3px}
.media h4{font-size:14px;font-weight:400;color:#fff}
.tabs{left:15px;top:43px;display:flex;gap:2px;font-size:10px;font-weight:700}
.tab{background:#f3f3f3;padding:6px 10px;height:24px;color:#222}
.tab.off{background:#fff}
.media-panel{left:15px;top:67px;width:256px;height:223px;background:#f3f3f3}
.video{left:11px;top:15px;width:233px;height:129px;background:linear-gradient(#8fa39f,#3e5a5a 45%,#133a44)}
.vbar{left:0;bottom:0;width:233px;height:14px;background:#111}
.media-panel a{font-size:10px;font-weight:700;color:#555}
.media-panel p{font-size:10px;color:#555}

/* view more */
.more-band{left:0;top:943px;width:960px;height:130px;background:linear-gradient(var(--pale),#fff);border-top:1px solid #d3dbe4}
.more-title{left:98px;top:915px;font-size:16px;color:var(--blue-deep)}
.more-text{left:98px;top:954px;width:200px;font-size:11.5px;line-height:17.6px;color:#555}
.thumb{width:108px;height:108px;border-radius:50%;border:3px solid var(--blue);top:890px}
.thumb-cap{top:1011px;font-size:11.5px;color:#555;line-height:15px;white-space:nowrap}
.thumb-cap b{font-family:"Bree Serif",Georgia,serif;font-weight:400;font-size:12.5px;color:var(--blue-deep);display:block}
</style>
</head>
<body>

<div class="abs utility-bar"></div>
<nav class="abs utility-nav"><span>Home</span><span>Best Practices Schools</span><span>Lurvikmeter</span><span>About Lurvik.no</span></nav>
<div class="abs search">search
  <svg width="11" height="11" viewBox="0 0 11 11"><circle cx="4.5" cy="4.5" r="3.3" fill="none" stroke="#8ab51e" stroke-width="1.6"/><line x1="7" y1="7" x2="10" y2="10" stroke="#8ab51e" stroke-width="1.8"/></svg>
</div>

<div class="abs logo">
  <div class="logo-mark"></div>
  <div><div class="logo-name">Lurvik</div><div class="logo-tag">Entreprenørielle metoder i undervisningen</div></div>
</div>

<div class="abs feature" style="left:352px">
  <div class="icon-circle"><svg width="22" height="20" viewBox="0 0 22 20"><rect x="2" y="2" width="18" height="14" fill="none" stroke="#fff" stroke-width="2"/><path d="M7 6v8M15 6v8" stroke="#fff" stroke-width="2"/></svg></div>
  <div><h3>What is Pedagogical<br>Entrepreneurship</h3><em>What, Why and How!</em></div>
</div>
<div class="abs feature" style="left:550px">
  <div class="icon-circle"><svg width="22" height="20" viewBox="0 0 22 20"><rect x="2" y="3" width="18" height="12" fill="none" stroke="#fff" stroke-width="2"/><path d="M6 8h8M6 11h5M11 15v4" stroke="#fff" stroke-width="1.6"/></svg></div>
  <div><h3>Methods and<br>Teaching Plans</h3><em>Plan your Lessons!</em></div>
</div>
<div class="abs feature" style="left:730px">
  <div class="icon-circle"><svg width="18" height="22" viewBox="0 0 18 22"><rect x="2" y="1" width="14" height="18" fill="none" stroke="#fff" stroke-width="2"/><path d="M5 6h8M5 9h8M5 12h5" stroke="#fff" stroke-width="1.5"/><circle cx="12" cy="16" r="3" fill="#fff"/></svg></div>
  <div><h3>Good Examples,<br>Best Practices</h3><em>Be Inspired!</em></div>
</div>

<div class="abs band"></div>

<div class="abs crumbs"><a href="#">Home</a><span>&gt;</span><a href="#">Good Examples</a><span>&gt;</span><span>Små TOPP i Vassbygd</span></div>
<div class="abs social" style="left:727px"><span class="btn"><i class="sq"></i>Like</span><span class="count">86</span></div>
<div class="abs social" style="left:798px"><span class="btn"><i class="sq"></i>Share</span><span class="count">30</span></div>
<div class="abs dash" style="left:95px;top:183px;width:766px"></div>

<h1 class="abs title serif" style="font-weight:400">Små-TOPP i Vassbygd</h1>
<p class="abs lead">Lorem ipsum dolor sit amet, consectetur adipiscing elit. Nam porttitor felis et elit egestas nec venenatis enim rhoncus.</p>
<p class="abs body" style="left:95px;top:283px">Maecenas lacus augue, dignissim vulputate eleifend vitae, scelerisque at sapien. Suspendisse diam felis, pulvinar vitae posuere eu, volutpat et urna. Vivamus vel leo justo, ut tincidunt ipsum. Curabitur justo orci, semper quis feugiat semper, dignissim a orci. Suspendisse nec ipsum sit amet nulla tincidunt vestibulum.</p>

<div class="abs fact" style="left:101px;top:371px">
  <div class="icon-circle"><svg width="22" height="22" viewBox="0 0 22 22"><circle cx="11" cy="12" r="8" fill="none" stroke="#fff" stroke-width="2"/><path d="M11 7v5l3 2" stroke="#fff" stroke-width="1.8" fill="none"/></svg></div>
  <div><b>Time Spent</b><span>Text</span></div>
</div>
<div class="abs fact" style="left:309px;top:371px">
  <div class="icon-circle"><svg width="22" height="22" viewBox="0 0 22 22"><rect x="3" y="5" width="13" height="13" fill="none" stroke="#fff" stroke-width="2"/><path d="M9 13l9-9 2 2-9 9H9z" fill="#fff"/></svg></div>
  <div><b>Subject</b><span>English, Norwegian, Maths</span></div>
</div>
<div class="abs fact" style="left:101px;top:436px">
  <div class="icon-circle"><svg width="22" height="22" viewBox="0 0 22 22"><circle cx="11" cy="4" r="2.2" fill="#fff"/><path d="M10 6L4 20M12 6l6 14M6 14h10" stroke="#fff" stroke-width="2" fill="none"/></svg></div>
  <div><b>Method</b><span>TOPP</span></div>
</div>

<div class="abs card-frame school">
  <div class="abs school-inner">
    <svg class="abs" style="left:18px;top:10px" width="28" height="24" viewBox="0 0 28 24"><path d="M2 12L14 2l12 10" stroke="#fff" stroke-width="2.5" fill="none"/><rect x="6" y="11" width="16" height="12" fill="#fff"/><rect x="12" y="16" width="4" height="7" fill="#1f5a96"/></svg>
    <div class="abs" style="left:60px;top:10px"><h4>Vassbygd skole</h4><small>4th Grade</small></div>
    <div class="abs photo-school" role="img" aria-label="Photo of the school building in winter"></div>
    <div class="abs contact">
      <svg class="abs" style="left:10px;top:12px" width="30" height="30" viewBox="0 0 30 30"><circle cx="15" cy="10" r="6" fill="#2a88c8"/><path d="M3 29c1-8 6-11 12-11s11 3 12 11z" fill="#2a88c8"/></svg>
      <div class="abs" style="left:56px;top:10px"><small>Contact</small><br><a href="#">Jane Doe</a></div>
    </div>
  </div>
</div>

<div class="abs dash green" style="left:95px;top:506px;width:766px"></div>

<h2 class="abs h-sub" style="left:95px;top:541px">This is how we did it</h2>
<p class="abs body" style="left:95px;top:563px">Maecenas lacus augue, dignissim vulputate eleifend vitae, scelerisque at sapien. Suspendisse diam felis, pulvinar vitae posuere eu, volutpat et urna. Vivamus vel leo justo, ut tincidunt ipsum. Curabitur justo orci, semper quis feugiat semper, dignissim a orci. Suspendisse nec ipsum sit amet nulla tincidunt vestibulum.</p>
<h2 class="abs h-sub" style="left:95px;top:645px">Title</h2>
<p class="abs body" style="left:95px;top:667px">Maecenas lacus augue, dignissim vulputate eleifend vitae, scelerisque at sapien. Suspendisse diam felis, pulvinar vitae posuere eu, volutpat et urna. Vivamus vel leo justo, ut tincidunt ipsum. Curabitur justo orci, semper quis feugiat semper, dignissim a orci. Suspendisse nec ipsum sit amet nulla tincidunt vestibulum.</p>
<h2 class="abs h-sub" style="left:95px;top:749px">Title</h2>
<p class="abs body" style="left:95px;top:771px">Maecenas lacus augue, dignissim vulputate eleifend vitae, scelerisque at sapien. Suspendisse diam felis, pulvinar vitae posuere eu, volutpat et urna. Vivamus vel leo justo, ut tincidunt ipsum. Curabitur justo orci, semper quis feugiat semper, dignissim a orci. Suspendisse nec ipsum sit amet nulla tincidunt vestibulum.</p>

<div class="abs card-frame media">
  <div class="abs media-inner">
    <svg class="abs" style="left:18px;top:14px" width="24" height="18" viewBox="0 0 24 18"><circle cx="5" cy="4" r="3" fill="none" stroke="#fff" stroke-width="1.6"/><circle cx="12" cy="4" r="3" fill="none" stroke="#fff" stroke-width="1.6"/><rect x="1" y="8" width="16" height="9" fill="none" stroke="#fff" stroke-width="1.6"/><path d="M18 11l5-3v9l-5-3z" fill="#fff"/></svg>
    <h4 class="abs serif" style="left:62px;top:16px">Multimedia</h4>
    <div class="abs tabs"><span class="tab">Videos (1)</span><span class="tab off">Images (4)</span></div>
    <div class="abs media-panel">
      <div class="abs video" role="img" aria-label="Video still of a stormy sea under a cloudy sky">
        <div class="abs vbar">
          <svg class="abs" style="left:12px;top:3px" width="7" height="8" viewBox="0 0 7 8"><path d="M0 0l7 4-7 4z" fill="#fff"/></svg>
          <div class="abs" style="left:34px;top:6px;width:156px;height:2px;background:#555"></div>
        </div>
      </div>
      <div class="abs" style="left:11px;top:157px"><a href="#">Ses video</a><p style="margin-top:4px">Short text about the video</p></div>
    </div>
  </div>
</div>

<div class="abs more-band"></div>
<h2 class="abs more-title serif" style="font-weight:400">View More Like This</h2>
<p class="abs more-text">Learn about some of the schools and systems that have incorporated pedagogical entrepreneurship best practices.</p>

<div class="abs thumb" style="left:375px;background:radial-gradient(#bbb,#444)" role="img" aria-label="Black and white photo of pupils working at a table"></div>
<div class="abs thumb-cap" style="left:387px"><b>Små-TOPP</b>at Vassbygd School</div>

<div class="abs thumb" style="left:547px;background:radial-gradient(#999,#222)" role="img" aria-label="Black and white photo of a pupil holding a book"></div>
<div class="abs thumb-cap" style="left:558px"><b>Idéverksted</b>at Fjellheim School</div>

<div class="abs thumb" style="left:720px;background:radial-gradient(#ddd,#555)" role="img" aria-label="Black and white photo of a vaulted stone hallway"></div>
<div class="abs thumb-cap" style="left:721px"><b>Kafé Læring</b>at Solbakken School</div>

</body>
</html>
```